LEARN Business Skills so you can Earn a good living

size of the poster is 8”x 10.75" plus 0.25" bleed.
Please leave 1 inch on the bottoum for footer
I want a design a poster that will attract people's attention.
I appreciate a creative ad however the ad should not take away from being able to clearly read the text.
-I also appreciate a simple creative ad that is not too busy.
-you can use graphics, vectors, or pictures of real people.
-however, if you use real people it should be a white male that is wearing a white shirt and look like a professional person.

Target Market(s)

Potential young business people

Industry/Entity Type

education

Requirements
Must have
• easy to read the text
Nice to have
• I would like a "creative" simple ad that is easy to be read
Should not have
• pictures of women

```html
<!DOCTYPE html>
<html lang="en">
<head>
<meta charset="utf-8">
<title>Learn to Earn – Business Prosperity Course</title>
<link rel="stylesheet" href="https://fonts.googleapis.com/css2?family=Poppins:wght@400;500;600;700;800&family=Roboto+Condensed:wght@700&display=swap">
<style>
  :root {
    --navy-top: #123f5c;
    --navy-mid: #0d2f48;
    --navy-bottom: #081c2e;
    --teal: #2aa3c3;
    --teal-light: #62c8da;
    --teal-deep: #1a87a8;
    --yellow: #f2e614;
    --white: #ffffff;
  }
  * { box-sizing: border-box; margin: 0; padding: 0; }
  html, body { width: 930px; height: 1200px; overflow: hidden; background: #ffffff; }
  .poster {
    position: relative;
    width: 930px;
    height: 1200px;
    overflow: hidden;
    font-family: "Poppins", sans-serif;
    color: var(--white);
    background: radial-gradient(ellipse at 50% 30%, var(--navy-top) 0%, var(--navy-mid) 55%, var(--navy-bottom) 100%);
  }
  .abs { position: absolute; }

  .title-frame { left: 0; top: 0; width: 930px; height: 320px; }
  .kicker {
    left: 0; width: 930px; top: 60px; text-align: center;
    font-size: 38px; font-weight: 500; letter-spacing: 3px; line-height: 1;
  }
  .headline-main {
    left: 0; width: 930px; top: 93px; text-align: center;
    font-size: 118px; font-weight: 700; letter-spacing: -1px; line-height: 1;
    background: linear-gradient(180deg, var(--teal-light) 0%, var(--teal) 50%, var(--teal-deep) 100%);
    -webkit-background-clip: text; background-clip: text; color: transparent;
  }
  .headline-sub {
    left: 0; width: 930px; top: 190px; text-align: center;
    font-size: 86px; font-weight: 700; letter-spacing: -1px; line-height: 1; color: var(--yellow);
  }
  .course-label {
    left: 0; width: 930px; top: 277px; text-align: center;
    font-size: 34px; font-weight: 500; line-height: 1; letter-spacing: 1px;
  }
  .tagline {
    left: 0; width: 930px; top: 323px; text-align: center;
    font-size: 22.5px; font-weight: 500; line-height: 1;
  }

  .hero-art {
    left: 150px; top: 388px; width: 696px; height: 394px;
    border-radius: 180px 200px 30px 30px;
    background: radial-gradient(ellipse at 50% 40%, #e6f4fb 0%, #b9def0 45%, #3a9fd0 80%, rgba(13,47,72,0) 100%);
  }

  .skills-heading {
    left: 0; width: 930px; top: 788px; text-align: center;
    font-family: "Roboto Condensed", sans-serif; font-weight: 700; font-size: 29px; line-height: 1;
  }
  .skills-heading .accent { color: var(--yellow); }
  .divider-dots { left: 0; top: 829px; width: 930px; height: 10px; }

  .benefit { top: 859px; height: 60px; }
  .benefit .pill {
    position: absolute; left: 29px; top: 8px; height: 44px; right: 0;
    border-radius: 0 22px 22px 0;
    background: linear-gradient(90deg, var(--teal) 0%, var(--teal-light) 100%);
    display: flex; align-items: center; padding-left: 38px;
    font-size: 19px; font-weight: 600; line-height: 1;
  }
  .benefit .badge {
    position: absolute; left: 0; top: 0; width: 60px; height: 60px; border-radius: 50%;
    background: var(--white); border: 3px solid var(--teal-deep);
    display: flex; align-items: center; justify-content: center; z-index: 1;
  }
  .benefit-job { left: 72px; width: 271px; }
  .benefit-business { left: 347px; width: 241px; }
  .benefit-salary { left: 619px; width: 239px; }

  .skill-list { list-style: none; top: 928px; }
  .skill-list li {
    position: absolute; left: 0; white-space: nowrap;
    font-size: 14px; font-weight: 400; letter-spacing: 0.3px; line-height: 16px;
    padding-left: 26px; text-transform: uppercase;
  }
  .skill-list li svg { position: absolute; left: 0; top: 0; width: 16px; height: 16px; }
  .col-1 { left: 78px; }
  .col-2 { left: 342px; }
  .col-3 { left: 564px; }
  .col-4 { left: 728px; }

  .enroll-bar {
    left: 113px; top: 1075px; width: 720px; height: 46px;
    border-radius: 18px 22px 22px 0;
    background: linear-gradient(90deg, var(--teal) 0%, var(--teal-light) 50%, var(--teal) 100%);
  }
  .enroll-label {
    left: 154px; top: 1080px; font-size: 34px; font-weight: 700; letter-spacing: 4px; line-height: 36px;
  }
  .phone-number {
    left: 535px; top: 1080px; font-size: 29px; font-weight: 700; letter-spacing: 2px; line-height: 36px;
  }
  .phone-badge {
    left: 441px; top: 1065px; width: 64px; height: 64px; border-radius: 50%;
    background: var(--white); border: 3px solid var(--navy-mid);
    display: flex; align-items: center; justify-content: center;
  }
  .website {
    left: 0; width: 930px; top: 1133px; text-align: center;
    font-size: 17px; font-weight: 500; letter-spacing: 4px; line-height: 20px;
  }
  .website .accent { color: var(--yellow); }
</style>
</head>
<body>
<main class="poster">

  <svg class="abs title-frame" viewBox="0 0 930 320" aria-hidden="true">
    <path d="M305 81 H153 V302 H375 M566 302 H789 V81 H637" fill="none" stroke="var(--teal)" stroke-width="3"/>
  </svg>
  <p class="abs kicker">LEARN to EARN</p>
  <h1 class="abs headline-main">BUSINESS</h1>
  <p class="abs headline-sub">PROSPERITY</p>
  <p class="abs course-label">COURSE</p>
  <p class="abs tagline">A proven success of helping people in their livelihoods</p>

  <div class="abs hero-art" role="img" aria-label="Illustration: online lesson on a large phone screen with two students on laptops, books, a light bulb and a rising arrow"></div>

  <h2 class="abs skills-heading"><span class="accent">BUSINESS SKILLS</span> THAT WILL HELP YOU</h2>
  <svg class="abs divider-dots" viewBox="0 0 930 10" aria-hidden="true">
    <rect x="426" y="1" width="3" height="8" fill="var(--teal)" opacity="0.4"/>
    <rect x="440" y="1" width="8" height="8" fill="var(--teal)"/>
    <rect x="459" y="1" width="8" height="8" fill="var(--teal)"/>
    <rect x="478" y="1" width="8" height="8" fill="var(--teal)"/>
    <rect x="497" y="1" width="3" height="8" fill="var(--teal)" opacity="0.4"/>
  </svg>

  <div class="abs benefit benefit-job">
    <div class="badge">
      <svg width="30" height="30" viewBox="0 0 30 30" aria-hidden="true">
        <path d="M10 17 L6 27 L10 25 L12 28 L15 20 Z M20 17 L24 27 L20 25 L18 28 L15 20 Z" fill="var(--navy-mid)"/>
        <circle cx="15" cy="12" r="9" fill="var(--navy-mid)"/>
        <circle cx="15" cy="12" r="5.5" fill="none" stroke="#fff" stroke-width="1.5"/>
        <path d="M15 8.5 L16 11 L18.5 11 L16.5 12.6 L17.3 15 L15 13.6 L12.7 15 L13.5 12.6 L11.5 11 L14 11 Z" fill="#fff"/>
      </svg>
    </div>
    <div class="pill">Get a quality job</div>
  </div>

  <div class="abs benefit benefit-business">
    <div class="badge">
      <svg width="30" height="30" viewBox="0 0 30 30" aria-hidden="true">
        <rect x="5" y="19" width="4" height="8" fill="var(--navy-mid)"/>
        <rect x="11" y="15" width="4" height="12" fill="var(--navy-mid)"/>
        <rect x="17" y="18" width="4" height="9" fill="var(--navy-mid)"/>
        <rect x="23" y="13" width="4" height="14" fill="var(--navy-mid)"/>
        <path d="M4 15 L11 8 L16 12 L25 4" fill="none" stroke="var(--navy-mid)" stroke-width="2.2"/>
        <path d="M20 3 H26 V9" fill="none" stroke="var(--navy-mid)" stroke-width="2.2"/>
      </svg>
    </div>
    <div class="pill">Start/Grow<br>your business</div>
  </div>

  <div class="abs benefit benefit-salary">
    <div class="badge">
      <svg width="30" height="30" viewBox="0 0 30 30" aria-hidden="true">
        <text x="15" y="11" text-anchor="middle" font-family="Poppins, sans-serif" font-weight="700" font-size="11" fill="var(--navy-mid)">$</text>
        <rect x="9" y="13" width="12" height="2.5" fill="var(--navy-mid)"/>
        <rect x="7" y="17.5" width="16" height="2.5" fill="var(--navy-mid)"/>
        <rect x="5" y="22" width="20" height="2.5" fill="var(--navy-mid)"/>
        <path d="M15 16 L11 21 H13.5 V26 H16.5 V21 H19 Z" fill="var(--teal-deep)"/>
      </svg>
    </div>
    <div class="pill">Increase your<br>salary</div>
  </div>

  <ul class="abs skill-list col-1">
    <li style="top:2px"><svg viewBox="0 0 16 16" aria-hidden="true"><circle cx="7" cy="9" r="6" fill="none" stroke="var(--yellow)" stroke-width="1.4"/><path d="M3.5 8.5 L7 12 L15 2" fill="none" stroke="var(--yellow)" stroke-width="2.4"/></svg>Business Administration</li>
    <li style="top:24px"><svg viewBox="0 0 16 16" aria-hidden="true"><circle cx="7" cy="9" r="6" fill="none" stroke="var(--yellow)" stroke-width="1.4"/><path d="M3.5 8.5 L7 12 L15 2" fill="none" stroke="var(--yellow)" stroke-width="2.4"/></svg>Small Business<br>Management</li>
    <li style="top:64px"><svg viewBox="0 0 16 16" aria-hidden="true"><circle cx="7" cy="9" r="6" fill="none" stroke="var(--yellow)" stroke-width="1.4"/><path d="M3.5 8.5 L7 12 L15 2" fill="none" stroke="var(--yellow)" stroke-width="2.4"/></svg>Finance</li>
    <li style="top:85px"><svg viewBox="0 0 16 16" aria-hidden="true"><circle cx="7" cy="9" r="6" fill="none" stroke="var(--yellow)" stroke-width="1.4"/><path d="M3.5 8.5 L7 12 L15 2" fill="none" stroke="var(--yellow)" stroke-width="2.4"/></svg>Investments</li>
    <li style="top:107px"><svg viewBox="0 0 16 16" aria-hidden="true"><circle cx="7" cy="9" r="6" fill="none" stroke="var(--yellow)" stroke-width="1.4"/><path d="M3.5 8.5 L7 12 L15 2" fill="none" stroke="var(--yellow)" stroke-width="2.4"/></svg>Computers</li>
  </ul>

  <ul class="abs skill-list col-2">
    <li style="top:2px"><svg viewBox="0 0 16 16" aria-hidden="true"><circle cx="7" cy="9" r="6" fill="none" stroke="var(--yellow)" stroke-width="1.4"/><path d="M3.5 8.5 L7 12 L15 2" fill="none" stroke="var(--yellow)" stroke-width="2.4"/></svg>Accounting</li>
    <li style="top:23px"><svg viewBox="0 0 16 16" aria-hidden="true"><circle cx="7" cy="9" r="6" fill="none" stroke="var(--yellow)" stroke-width="1.4"/><path d="M3.5 8.5 L7 12 L15 2" fill="none" stroke="var(--yellow)" stroke-width="2.4"/></svg>Sales&nbsp; Marketing</li>
    <li style="top:46px"><svg viewBox="0 0 16 16" aria-hidden="true"><circle cx="7" cy="9" r="6" fill="none" stroke="var(--yellow)" stroke-width="1.4"/><path d="M3.5 8.5 L7 12 L15 2" fill="none" stroke="var(--yellow)" stroke-width="2.4"/></svg>Project Management<br>Interviewing Skills</li>
    <li style="top:85px"><svg viewBox="0 0 16 16" aria-hidden="true"><circle cx="7" cy="9" r="6" fill="none" stroke="var(--yellow)" stroke-width="1.4"/><path d="M3.5 8.5 L7 12 L15 2" fill="none" stroke="var(--yellow)" stroke-width="2.4"/></svg>Business Law</li>
    <li style="top:107px"><svg viewBox="0 0 16 16" aria-hidden="true"><circle cx="7" cy="9" r="6" fill="none" stroke="var(--yellow)" stroke-width="1.4"/><path d="M3.5 8.5 L7 12 L15 2" fill="none" stroke="var(--yellow)" stroke-width="2.4"/></svg>Bookkeeping</li>
  </ul>

  <ul class="abs skill-list col-3">
    <li style="top:2px"><svg viewBox="0 0 16 16" aria-hidden="true"><circle cx="7" cy="9" r="6" fill="none" stroke="var(--yellow)" stroke-width="1.4"/><path d="M3.5 8.5 L7 12 L15 2" fill="none" stroke="var(--yellow)" stroke-width="2.4"/></svg>Negotiation</li>
    <li style="top:23px"><svg viewBox="0 0 16 16" aria-hidden="true"><circle cx="7" cy="9" r="6" fill="none" stroke="var(--yellow)" stroke-width="1.4"/><path d="M3.5 8.5 L7 12 L15 2" fill="none" stroke="var(--yellow)" stroke-width="2.4"/></svg>Public Speaking</li>
    <li style="top:45px"><svg viewBox="0 0 16 16" aria-hidden="true"><circle cx="7" cy="9" r="6" fill="none" stroke="var(--yellow)" stroke-width="1.4"/><path d="M3.5 8.5 L7 12 L15 2" fill="none" stroke="var(--yellow)" stroke-width="2.4"/></svg>Import/Export</li>
    <li style="top:68px"><svg viewBox="0 0 16 16" aria-hidden="true"><circle cx="7" cy="9" r="6" fill="none" stroke="var(--yellow)" stroke-width="1.4"/><path d="M3.5 8.5 L7 12 L15 2" fill="none" stroke="var(--yellow)" stroke-width="2.4"/></svg>Information<br>Technology</li>
    <li style="top:107px"><svg viewBox="0 0 16 16" aria-hidden="true"><circle cx="7" cy="9" r="6" fill="none" stroke="var(--yellow)" stroke-width="1.4"/><path d="M3.5 8.5 L7 12 L15 2" fill="none" stroke="var(--yellow)" stroke-width="2.4"/></svg>Marketing</li>
  </ul>

  <ul class="abs skill-list col-4">
    <li style="top:6px"><svg viewBox="0 0 16 16" aria-hidden="true"><circle cx="7" cy="9" r="6" fill="none" stroke="var(--yellow)" stroke-width="1.4"/><path d="M3.5 8.5 L7 12 L15 2" fill="none" stroke="var(--yellow)" stroke-width="2.4"/></svg>Real Estate</li>
    <li style="top:29px"><svg viewBox="0 0 16 16" aria-hidden="true"><circle cx="7" cy="9" r="6" fill="none" stroke="var(--yellow)" stroke-width="1.4"/><path d="M3.5 8.5 L7 12 L15 2" fill="none" stroke="var(--yellow)" stroke-width="2.4"/></svg>Health Care</li>
    <li style="top:52px"><svg viewBox="0 0 16 16" aria-hidden="true"><circle cx="7" cy="9" r="6" fill="none" stroke="var(--yellow)" stroke-width="1.4"/><path d="M3.5 8.5 L7 12 L15 2" fill="none" stroke="var(--yellow)" stroke-width="2.4"/></svg>Management</li>
    <li style="top:75px"><svg viewBox="0 0 16 16" aria-hidden="true"><circle cx="7" cy="9" r="6" fill="none" stroke="var(--yellow)" stroke-width="1.4"/><path d="M3.5 8.5 L7 12 L15 2" fill="none" stroke="var(--yellow)" stroke-width="2.4"/></svg>E-Commerce</li>
    <li style="top:100px"><svg viewBox="0 0 16 16" aria-hidden="true"><circle cx="7" cy="9" r="6" fill="none" stroke="var(--yellow)" stroke-width="1.4"/><path d="M3.5 8.5 L7 12 L15 2" fill="none" stroke="var(--yellow)" stroke-width="2.4"/></svg>Distribution</li>
  </ul>

  <div class="abs enroll-bar"></div>
  <p class="abs enroll-label">ENROLL NOW</p>
  <div class="abs phone-badge">
    <svg width="34" height="34" viewBox="0 0 24 24" aria-hidden="true">
      <path d="M6.6 10.8c1.4 2.8 3.8 5.1 6.6 6.6l2.2-2.2c.3-.3.7-.4 1-.2 1.1.4 2.3.6 3.6.6.6 0 1 .4 1 1V20c0 .6-.4 1-1 1C10.6 21 3 13.4 3 4c0-.6.4-1 1-1h3.5c.6 0 1 .4 1 1 0 1.3.2 2.5.6 3.6.1.3 0 .7-.2 1L6.6 10.8z" fill="var(--navy-bottom)"/>
    </svg>
  </div>
  <p class="abs phone-number">011 555 010 2847</p>
  <p class="abs website">www.<span class="accent">prosperityskillshub</span>.com</p>

</main>
</body>
</html>
```